TalkHarbor - Language Coaching Services

Sleek, innovative, trendy design for Language Coaching business.

TalkHarbor is a new UK based company that provides Language Coaching services. We offer highly personalized on-line and face to face language courses. We also impart learning techniques workshops based on the latest neuroscience research for second-language acquisition.

Target Market(s)

See attached info

Industry/Entity Type

Consulting

Contact Information for Business Card

TalkHarbor
DaniaKV@talkharbor.co.uk
TalkHarbor.co.uk
London, UK

Font styles to use
Sans Serif

```html
<!DOCTYPE html>
<html lang="en">
<head>
<meta charset="utf-8">
<title>TalkHarbor Business Card</title>
<link rel="stylesheet" href="https://fonts.googleapis.com/css2?family=Roboto:wght@300;400;500;700&display=swap">
<style>
  :root {
    --page-bg: #e4e4e4;
    --card-white: #ffffff;
    --brand-blue: #0a88c4;
    --brand-blue-deep: #0a6fa3;
    --back-light: #0bb2e8;
    --back-dark: #04577f;
    --text-grey: #555a5e;
    --title-grey: #9a9a9a;
  }
  * { margin: 0; padding: 0; box-sizing: border-box; }
  html, body {
    width: 1125px; height: 1200px; overflow: hidden;
    background: var(--page-bg);
    font-family: "Roboto", Arial, sans-serif;
  }
  .card {
    position: absolute; left: 150px; width: 825px; height: 470px;
    border-radius: 26px; overflow: hidden;
  }
  .card--front { top: 98px; background: var(--card-white); }
  .card--back {
    top: 630px;
    background: radial-gradient(ellipse 60% 65% at 50% 50%, var(--back-light) 0%, var(--brand-blue) 50%, var(--back-dark) 100%);
  }
  .brand-art {
    position: absolute; left: 10px; top: 0; width: 420px; height: 470px;
    background: linear-gradient(90deg, rgba(10,136,196,0.14) 0%, rgba(10,136,196,0.05) 100%);
  }
  .contact {
    position: absolute; right: 52px; top: 172px; text-align: right; color: var(--text-grey);
  }
  .contact__name {
    font-size: 30px; font-weight: 700; color: var(--brand-blue-deep); letter-spacing: 0.5px; line-height: 1;
  }
  .contact__title {
    font-size: 20px; font-weight: 500; color: var(--title-grey); margin-top: 4px; letter-spacing: 0.5px;
  }
  .contact__city { font-size: 19px; margin-top: 20px; }
  .contact__lines { margin-top: 14px; font-size: 19px; line-height: 26px; }
  .contact__line { display: flex; justify-content: flex-end; align-items: center; gap: 8px; }
  .contact__line svg { width: 18px; height: 18px; flex: none; }
  .wordmark {
    font-weight: 500; letter-spacing: 1px; line-height: 1;
  }
  .wordmark--front {
    position: absolute; right: 52px; bottom: 38px; font-size: 48px; color: var(--brand-blue);
  }
  .back-lockup {
    position: absolute; left: 0; right: 0; top: 124px;
    display: flex; flex-direction: column; align-items: center; gap: 22px;
  }
  .back-lockup__circle {
    width: 156px; height: 156px; border-radius: 50%; border: 9px solid var(--card-white);
  }
  .wordmark--back { font-size: 60px; color: var(--card-white); }
</style>
</head>
<body>
  <section class="card card--front">
    <div class="brand-art" role="img" aria-label="Large brand symbol decoration"></div>
    <div class="contact">
      <p class="contact__name">OWEN HALE</p>
      <p class="contact__title">CEO/FOUNDER</p>
      <p class="contact__city">London, UK</p>
      <div class="contact__lines">
        <p class="contact__line">612 408 3917
          <svg viewBox="0 0 18 18" aria-hidden="true"><rect x="5" y="1.5" width="8" height="15" rx="1.5" fill="none" stroke="var(--brand-blue)" stroke-width="1.6"/><rect x="7.5" y="13.5" width="3" height="1.2" fill="var(--brand-blue)"/></svg>
        </p>
        <p class="contact__line">DaniaKV@talkharbor.co.uk
          <svg viewBox="0 0 18 18" aria-hidden="true"><rect x="1.5" y="4" width="15" height="10" fill="var(--brand-blue)"/><path d="M1.5 4 L9 10 L16.5 4" fill="none" stroke="#fff" stroke-width="1.3"/></svg>
        </p>
        <p class="contact__line">TalkHarbor.co.uk
          <svg viewBox="0 0 18 18" aria-hidden="true"><circle cx="9" cy="9" r="7.5" fill="var(--brand-blue)"/><path d="M4 7 Q7 5 8 8 Q9 11 7 13 M11 4 Q13 7 14 10" fill="none" stroke="#fff" stroke-width="1.4"/></svg>
        </p>
      </div>
    </div>
    <p class="wordmark wordmark--front">TALKHARBOR</p>
  </section>

  <section class="card card--back">
    <div class="back-lockup">
      <div class="back-lockup__circle"></div>
      <p class="wordmark wordmark--back">TALKHARBOR</p>
    </div>
  </section>
</body>
</html>
```